Need exciting and bold trade show booth design

We focus on Roofing, Siding, Gutters.
We do both retail & insurance (Storm Damage) work. We offer financing.
We are an Halvery Brisk Preferred Contractor.
The following are just my thoughts:
Maybe have half of the backdrop to focus on insurance and half to focus on retail. Maybe have one side white with blue letters and one side white with blue letters? Maybe have the logo in the ,middle to separate the two sides? On the storm damage side have a storm and on the retail side have a calm sky? I am thank the stand alone display will have explained the warranty? Maybe have the highlight the four small sections won my website..... "Affordable Rates, Quick Response, Experienced Team, Veteran Owned."
5 Displays need graphics
10x10 display
Monitor display - logo with company name and logo only. Maybe a slogan added and/or graphic added.
Podium display - logo with company name or logo only. Maybe slogan added and/or graphic added.
Header Display - logo with name only
Stand alone display - Logo with company name and warranty workmanship information, "LSP". We offer a lifetime workmanship warranty, the "Lantern Safeguard Pledge". I would like the stand alone banner to display the information about our "LSP" workmanship warranty.
Check out our website for more information.
www.tmdshingleworks.net.
Target Market(s)
Potential roofing siding and gutter customers
Industry/Entity Type
Roofing
Requirements
Must have
- Veteran Owned & Operated.

```html
<!DOCTYPE html>
<html lang="en">
<head>
<meta charset="utf-8">
<title>TMD Shingle Works – Trade Show Booth Graphics</title>
<link rel="stylesheet" href="https://fonts.googleapis.com/css2?family=Montserrat:wght@500;600;700;800;900&family=Oswald:wght@500;700&display=swap">
<style>
  :root {
    --brand-blue: #1f86d6;
    --deep-blue: #15488f;
    --royal-blue: #1a5fb4;
    --panel-blue: #1f70bf;
    --bright-blue: #1a8fe3;
    --cyan: #19b5d6;
    --gold: #f5b800;
    --red: #e3261b;
    --green: #3bb54a;
    --lime: #6cc24a;
    --charcoal: #2f2f31;
    --ink: #222;
    --white: #fff;
    --wrap-grey: #b3b3b3;
  }
  html, body {
    margin: 0;
    width: 1200px;
    height: 2730px;
    overflow: hidden;
  }
  body {
    position: relative;
    background: radial-gradient(ellipse 90% 60% at 50% 25%, #7a7a7a 0%, #555 55%, #2e2e2e 100%);
    font-family: "Montserrat", Arial, sans-serif;
  }
  .layout-title {
    position: absolute;
    transform: translateX(-50%);
    margin: 0;
    font: 700 39px/48px "Montserrat", Arial, sans-serif;
    color: #f2f2f2;
    white-space: nowrap;
  }
  .piece {
    position: absolute;
    display: block;
    box-shadow: 0 6px 14px rgba(0,0,0,.35);
  }
  .piece--header   { left: 191px; top: 136px; }
  .piece--booth    { left: 192px; top: 435px; }
  .piece--banner   { left: 238px; top: 1142px; }
  .piece--monitor  { left: 709px; top: 1142px; }
  .piece--podium   { left: 128px; top: 2195px; }
  .monitor-screen {
    position: absolute;
    left: 678px; top: 1335px;
    width: 336px; height: 191px;
    box-sizing: border-box;
    padding: 4px 4px 9px;
    background: #1c1c1e;
    border-radius: 3px;
    box-shadow: 0 6px 14px rgba(0,0,0,.45);
  }
  .monitor-screen .screen-image {
    width: 100%; height: 100%;
    background: linear-gradient(180deg, #d9b7cf 0%, #c5a3c6 35%, #98a8cc 55%, #6f8fb6 78%, #4d6c94 100%);
  }
  .brand-name   { fill: var(--brand-blue); font-family: "Montserrat", Arial, sans-serif; font-weight: 800; }
  .condensed    { font-family: "Oswald", "Arial Narrow", sans-serif; font-weight: 700; }
  .sans         { font-family: "Montserrat", Arial, sans-serif; }
</style>
</head>
<body>

<h2 class="layout-title" style="left:592px; top:71px;">Header Layout</h2>
<svg class="piece piece--header" width="819" height="185" viewBox="0 0 819 185">
  <rect width="819" height="185" fill="var(--white)"/>
  <rect x="20" y="18" width="779" height="149" rx="30" fill="none" stroke="#333" stroke-width="1.5" stroke-dasharray="8 6"/>
  <rect x="26" y="24" width="767" height="137" rx="30" fill="none" stroke="var(--green)" stroke-width="1.5"/>
  <circle cx="104" cy="92" r="52" fill="var(--brand-blue)"/>
  <text class="brand-name" x="178" y="92" font-size="58">TMD</text>
  <text class="brand-name" x="180" y="128" font-size="22" letter-spacing="5">SHINGLE WORKS</text>
  <line x1="514" y1="45" x2="514" y2="140" stroke="var(--brand-blue)" stroke-width="2"/>
  <text class="sans" x="537" y="80" font-size="27" font-weight="800" fill="var(--red)">Veteran Owned</text>
  <text class="sans" x="537" y="112" font-size="27" font-weight="800" fill="var(--red)">Small Business</text>
</svg>

<h2 class="layout-title" style="left:586px; top:370px;">10X10 Curved Display</h2>
<svg class="piece piece--booth" width="816" height="591" viewBox="0 0 816 591">
  <defs>
    <linearGradient id="booth-sky" x1="0" x2="1" y1="0" y2="0">
      <stop offset="0" stop-color="#15152a"/>
      <stop offset=".42" stop-color="#2b2845"/>
      <stop offset=".56" stop-color="#1b4f9c"/>
      <stop offset="1" stop-color="#2a78d2"/>
    </linearGradient>
    <linearGradient id="booth-mascot" x1="0" x2="0" y1="0" y2="1">
      <stop offset="0" stop-color="#f6c1d6"/>
      <stop offset="1" stop-color="#e57aa7"/>
    </linearGradient>
    <linearGradient id="booth-homes" x1="0" x2="1" y1="0" y2="1">
      <stop offset="0" stop-color="#8e9bab"/>
      <stop offset="1" stop-color="#b9ae98"/>
    </linearGradient>
    <linearGradient id="booth-badge" x1="0" x2="1" y1="0" y2="1">
      <stop offset="0" stop-color="#c8282e"/>
      <stop offset="1" stop-color="#1f3f8a"/>
    </linearGradient>
    <path id="badge-arc-top" d="M601,150 A47,47 0 0 1 695,150"/>
    <path id="badge-arc-bottom" d="M593,150 A55,55 0 0 0 703,150"/>
  </defs>
  <rect width="816" height="591" fill="var(--charcoal)"/>
  <rect y="90" width="816" height="350" fill="url(#booth-sky)" role="img" aria-label="Storm clouds with lightning on the left, calm blue sky over water on the right"/>
  <path d="M0,0H816V108Q408,260 0,108Z" fill="var(--white)"/>
  <rect x="12" y="13" width="793" height="568" rx="30" fill="none" stroke="#777" stroke-width="2" stroke-dasharray="8 6"/>
  <rect x="71" y="45" width="673" height="506" fill="none" stroke="var(--green)" stroke-width="1.5"/>

  <circle cx="279" cy="108" r="52" fill="var(--brand-blue)"/>
  <text class="brand-name" x="350" y="104" font-size="56">TMD</text>
  <text class="brand-name" x="352" y="140" font-size="19" letter-spacing="4">SHINGLE WORKS</text>

  <g class="veteran-badge">
    <circle cx="648" cy="150" r="57" fill="var(--white)"/>
    <circle cx="648" cy="150" r="36" fill="url(#booth-badge)" role="img" aria-label="Flag with saluting soldier silhouette"/>
    <text class="sans" font-size="10" font-weight="800" letter-spacing="2" fill="var(--ink)">
      <textPath href="#badge-arc-top" startOffset="50%" text-anchor="middle">VETERAN OWNED</textPath>
    </text>
    <text class="sans" font-size="10" font-weight="800" letter-spacing="2" fill="var(--ink)">
      <textPath href="#badge-arc-bottom" startOffset="50%" text-anchor="middle">OPERATED</textPath>
    </text>
  </g>

  <rect x="327" y="159" width="127" height="188" rx="14" fill="url(#booth-mascot)" role="img" aria-label="Cartoon mascot in a hard hat"/>

  <g class="service-list" fill="var(--white)">
    <circle cx="146" cy="218" r="10" fill="none" stroke="var(--white)" stroke-width="3"/>
    <circle cx="146" cy="260" r="10" fill="none" stroke="var(--white)" stroke-width="3"/>
    <circle cx="146" cy="300" r="10" fill="none" stroke="var(--white)" stroke-width="3"/>
    <text class="sans" x="165" y="230" font-size="33" font-weight="600">ROOFING</text>
    <text class="sans" x="165" y="272" font-size="33" font-weight="600">SIDING</text>
    <text class="sans" x="165" y="312" font-size="33" font-weight="600">GUTTERS</text>
  </g>

  <g class="market-list sans" fill="var(--white)" text-anchor="middle">
    <text x="593" y="225" font-size="20" font-weight="700">Retail • Insurance</text>
    <text x="593" y="250" font-size="20" font-weight="700">Residential • Commercial</text>
    <text x="593" y="284" font-size="30" font-weight="800">WE HAVE YOU</text>
    <rect x="479" y="291" width="227" height="39" rx="4" fill="var(--white)"/>
    <text x="593" y="323" font-size="37" font-weight="800" fill="var(--royal-blue)">COVERED</text>
  </g>

  <polygon points="39,347 746,347 775,440 71,440" fill="var(--white)"/>
  <g role="img" aria-label="Five photos of homes with new roofs">
    <polygon points="47,353 179,353 206,434 74,434" fill="url(#booth-homes)"/>
    <polygon points="188,353 320,353 347,434 215,434" fill="url(#booth-homes)"/>
    <polygon points="329,353 461,353 488,434 356,434" fill="url(#booth-homes)"/>
    <polygon points="470,353 602,353 629,434 497,434" fill="url(#booth-homes)"/>
    <polygon points="611,353 743,353 770,434 638,434" fill="url(#booth-homes)"/>
  </g>

  <text class="sans" x="408" y="502" font-size="58" font-weight="800" fill="var(--white)" text-anchor="middle">877-ROOF-TMD</text>
  <line x1="103" y1="538" x2="247" y2="538" stroke="var(--bright-blue)" stroke-width="1.5"/>
  <line x1="568" y1="538" x2="712" y2="538" stroke="var(--bright-blue)" stroke-width="1.5"/>
  <text class="sans" x="408" y="537" font-size="22" font-weight="700" fill="var(--white)" text-anchor="middle">www.<tspan fill="#3aa0e8">tmdshingleworks</tspan>.net</text>
</svg>

<h2 class="layout-title" style="left:385px; top:1076px;">Stand Alone Display</h2>
<svg class="piece piece--banner" width="281" height="936" viewBox="0 0 281 936">
  <defs>
    <linearGradient id="banner-umbrella" x1="0" x2="0" y1="0" y2="1">
      <stop offset="0" stop-color="#3aa8ee"/>
      <stop offset="1" stop-color="#1565b8"/>
    </linearGradient>
  </defs>
  <rect width="281" height="936" fill="var(--white)"/>
  <rect y="230" width="281" height="300" fill="#f3f5f8"/>

  <circle cx="55" cy="72" r="33" fill="var(--brand-blue)"/>
  <text class="brand-name" x="98" y="68" font-size="30">TMD</text>
  <text class="brand-name" x="99" y="88" font-size="14" letter-spacing="2">SHINGLE WORKS</text>

  <text class="condensed" x="140" y="172" font-size="56" fill="var(--bright-blue)" text-anchor="middle">PROUDLY</text>
  <polygon points="34,178 262,178 248,224 20,224" fill="var(--deep-blue)"/>
  <text class="condensed" x="141" y="214" font-size="36" fill="var(--white)" text-anchor="middle">OFFERS THE</text>

  <path d="M18,322 Q140,148 262,322 Z" fill="url(#banner-umbrella)" role="img" aria-label="Blue umbrella"/>

  <polygon points="46,343 252,343 240,383 34,383" fill="var(--deep-blue)"/>
  <text class="condensed" x="143" y="376" font-size="38" fill="var(--white)" text-anchor="middle">LANTERN</text>
  <polygon points="28,383 266,383 254,425 16,425" fill="var(--cyan)"/>
  <text class="condensed" x="141" y="418" font-size="40" fill="var(--white)" text-anchor="middle">SAFEGUARD</text>
  <polygon points="76,425 214,425 202,462 64,462" fill="var(--gold)"/>
  <text class="condensed" x="139" y="456" font-size="36" fill="var(--deep-blue)" text-anchor="middle">PLEDGE</text>

  <text class="condensed" x="140" y="495" font-size="24" fill="var(--deep-blue)" text-anchor="middle" textLength="216">LIFETIME WORKMANSHIP</text>
  <text class="sans" x="140" y="523" font-size="33" font-weight="900" fill="var(--red)" text-anchor="middle">WARRANTY</text>

  <path d="M0,562 Q150,548 281,518 V845 Q150,822 0,812 Z" fill="var(--panel-blue)"/>

  <g class="benefits" fill="var(--white)">
    <g class="benefit">
      <circle cx="65" cy="591" r="19" fill="var(--white)"/>
      <text class="sans" x="65" y="598" font-size="19" font-weight="800" fill="var(--panel-blue)" text-anchor="middle">$</text>
      <line x1="107" y1="567" x2="107" y2="615" stroke="var(--white)" stroke-width="1.5"/>
      <text class="sans" x="125" y="587" font-size="17" font-weight="600">Affordable</text>
      <text class="sans" x="125" y="607" font-size="17" font-weight="600">Rates</text>
    </g>
    <g class="benefit">
      <circle cx="65" cy="648" r="19" fill="var(--white)"/>
      <path d="M57,652 A9,9 0 1 1 67,657" fill="none" stroke="var(--panel-blue)" stroke-width="3"/>
      <polygon points="52,648 62,648 57,656" fill="var(--panel-blue)"/>
      <line x1="107" y1="624" x2="107" y2="672" stroke="var(--white)" stroke-width="1.5"/>
      <text class="sans" x="125" y="644" font-size="17" font-weight="600">Quick</text>
      <text class="sans" x="125" y="664" font-size="17" font-weight="600">Response</text>
    </g>
    <g class="benefit">
      <circle cx="65" cy="702" r="19" fill="var(--white)"/>
      <circle cx="59" cy="696" r="4.5" fill="var(--panel-blue)"/>
      <circle cx="71" cy="696" r="4.5" fill="var(--panel-blue)"/>
      <path d="M51,712 Q59,700 65,712 Z M65,712 Q71,700 79,712 Z" fill="var(--panel-blue)"/>
      <line x1="107" y1="678" x2="107" y2="726" stroke="var(--white)" stroke-width="1.5"/>
      <text class="sans" x="125" y="698" font-size="17" font-weight="600">Experienced</text>
      <text class="sans" x="125" y="718" font-size="17" font-weight="600">Team</text>
    </g>
    <g class="benefit">
      <circle cx="65" cy="755" r="19" fill="var(--white)"/>
      <rect x="54" y="746" width="22" height="16" fill="none" stroke="var(--panel-blue)" stroke-width="2"/>
      <line x1="54" y1="751" x2="76" y2="751" stroke="var(--panel-blue)" stroke-width="1.5"/>
      <line x1="54" y1="756" x2="76" y2="756" stroke="var(--panel-blue)" stroke-width="1.5"/>
      <rect x="54" y="746" width="8" height="6" fill="var(--panel-blue)"/>
      <line x1="107" y1="731" x2="107" y2="779" stroke="var(--white)" stroke-width="1.5"/>
      <text class="sans" x="125" y="751" font-size="17" font-weight="600">Veteran</text>
      <text class="sans" x="125" y="771" font-size="17" font-weight="600">Owned</text>
    </g>
  </g>

  <rect x="29" y="794" width="222" height="31" rx="15" fill="var(--gold)"/>
  <text class="sans" x="140" y="818" font-size="23" font-weight="800" fill="var(--white)" text-anchor="middle">877-ROOF-TMD</text>

  <rect x="42" y="840" width="80" height="28" rx="3" fill="#1f5fa8"/>
  <rect x="138" y="840" width="28" height="28" fill="#d6262b"/>
  <text class="condensed" x="172" y="853" font-size="13" font-weight="500" fill="var(--ink)">PREFERRED</text>
  <text class="condensed" x="172" y="867" font-size="13" font-weight="500" fill="var(--ink)">CONTRACTOR</text>

  <text class="sans" x="140" y="898" font-size="18" font-weight="500" fill="var(--ink)" text-anchor="middle">www.<tspan fill="var(--brand-blue)">tmdshingleworks</tspan>.net</text>
  <line x1="0" y1="920" x2="281" y2="920" stroke="#aaa" stroke-dasharray="4 3"/>
</svg>

<h2 class="layout-title" style="left:834px; top:1076px;">Montior Stand</h2>
<svg class="piece piece--monitor" width="252" height="934" viewBox="0 0 252 934">
  <rect width="252" height="934" fill="#f3f4f6"/>
  <rect x="29" y="35" width="193" height="888" fill="none" stroke="var(--lime)" stroke-width="3" stroke-dasharray="12 8"/>

  <circle cx="65" cy="81" r="23" fill="var(--brand-blue)"/>
  <text class="brand-name" x="96" y="80" font-size="24">TMD</text>
  <text class="brand-name" x="97" y="96" font-size="11" letter-spacing="1.5">SHINGLE WORKS</text>

  <text class="sans" x="126" y="136" font-size="17" font-weight="700" fill="#333" text-anchor="middle">TRUSTED BY</text>
  <text class="condensed" x="126" y="163" font-size="24" fill="var(--royal-blue)" text-anchor="middle">PROPERTY OWNERS</text>
  <text class="sans" x="126" y="184" font-size="17" font-weight="700" fill="#333" text-anchor="middle">JUST LIKE YOU</text>

  <polygon points="45,399 211,399 205,417 39,417" fill="var(--royal-blue)"/>
  <text class="sans" x="125" y="412" font-size="11" font-weight="600" fill="var(--white)" text-anchor="middle">www.tmdshingleworks.net</text>
  <text class="sans" x="122" y="518" font-size="13" font-weight="500" fill="#444" text-anchor="middle">SHELF 1</text>
  <rect y="521" width="252" height="6" fill="#8a8c90"/>

  <polygon points="45,541 211,541 205,559 39,559" fill="var(--royal-blue)"/>
  <text class="sans" x="125" y="554" font-size="11" font-weight="600" fill="var(--white)" text-anchor="middle">www.tmdshingleworks.net</text>
  <text class="sans" x="122" y="655" font-size="13" font-weight="500" fill="#444" text-anchor="middle">SHELF 2</text>
  <rect y="658" width="252" height="6" fill="#8a8c90"/>

  <g class="service-pills sans" font-size="17" font-weight="800" fill="var(--royal-blue)" text-anchor="middle">
    <rect x="56" y="704" width="140" height="24" rx="12" fill="var(--white)" stroke="var(--royal-blue)" stroke-width="2"/>
    <text x="126" y="722">ROOFING</text>
    <rect x="56" y="741" width="140" height="24" rx="12" fill="var(--white)" stroke="var(--royal-blue)" stroke-width="2"/>
    <text x="126" y="759">SIDING</text>
    <rect x="56" y="778" width="140" height="24" rx="12" fill="var(--white)" stroke="var(--royal-blue)" stroke-width="2"/>
    <text x="126" y="796">GUTTERS</text>
  </g>

  <circle cx="68" cy="853" r="23" fill="var(--brand-blue)"/>
  <text class="brand-name" x="99" y="852" font-size="24">TMD</text>
  <text class="brand-name" x="100" y="868" font-size="11" letter-spacing="1.5">SHINGLE WORKS</text>
</svg>
<div class="monitor-screen">
  <div class="screen-image" role="img" aria-label="Calm lake at sunset with a wooden pier"></div>
</div>

<h2 class="layout-title" style="left:609px; top:2128px;">Podium Layout</h2>
<svg class="piece piece--podium" width="943" height="397" viewBox="0 0 943 397">
  <rect width="943" height="397" fill="var(--white)"/>
  <rect width="943" height="40" fill="var(--wrap-grey)"/>
  <line x1="0" y1="41" x2="943" y2="41" stroke="#333" stroke-dasharray="2 2"/>
  <text class="sans" x="471" y="18" font-size="10" font-weight="700" fill="var(--ink)" text-anchor="middle">Wrap Zone</text>
  <text class="sans" x="471" y="29" font-size="7" font-weight="500" fill="var(--ink)" text-anchor="middle">(Extend background to cover this section)</text>

  <path d="M0,232 Q471,118 943,227 V354 H0 Z" fill="var(--panel-blue)"/>
  <path d="M0,232 Q471,118 943,227" fill="none" stroke="#1d9ae6" stroke-width="6"/>

  <rect y="354" width="943" height="43" fill="var(--wrap-grey)"/>
  <line x1="0" y1="354" x2="943" y2="354" stroke="#333" stroke-width="1"/>
  <text class="sans" x="471" y="373" font-size="10" font-weight="700" fill="var(--ink)" text-anchor="middle">Wrap Zone</text>
  <text class="sans" x="471" y="384" font-size="7" font-weight="500" fill="var(--ink)" text-anchor="middle">(Extend background to cover this section)</text>

  <g fill="none" stroke="var(--lime)" stroke-width="1.5" stroke-dasharray="8 6">
    <rect x="182" y="69" width="114" height="261"/>
    <rect x="326" y="69" width="261" height="261"/>
    <rect x="650" y="69" width="113" height="261"/>
  </g>

  <circle cx="413" cy="122" r="23" fill="var(--brand-blue)"/>
  <text class="brand-name" x="445" y="121" font-size="26">TMD</text>
  <text class="brand-name" x="446" y="137" font-size="11" letter-spacing="1.5">SHINGLE WORKS</text>
  <g class="sans" fill="var(--white)" text-anchor="middle">
    <text x="464" y="216" font-size="18" font-weight="800">RESIDENTIAL AND</text>
    <text x="464" y="238" font-size="18" font-weight="800">COMMERCIAL</text>
    <line x1="380" y1="253" x2="549" y2="253" stroke="var(--white)"/>
    <text x="464" y="282" font-size="17" font-weight="700">877-ROOF-TMD</text>
    <rect x="371" y="290" width="187" height="18" rx="9" fill="none" stroke="var(--white)"/>
    <text x="464" y="303" font-size="10.5" font-weight="600" letter-spacing="1">www.tmdshingleworks.net</text>
  </g>

  <g class="podium-side">
    <circle cx="239" cy="111" r="17" fill="var(--brand-blue)"/>
    <text class="brand-name" x="239" y="152" font-size="16" text-anchor="middle">TMD</text>
    <text class="brand-name" x="239" y="163" font-size="7" letter-spacing="1" text-anchor="middle">SHINGLE WORKS</text>
    <g stroke="var(--white)" stroke-width="1">
      <line x1="199" y1="245" x2="233" y2="245"/><line x1="245" y1="245" x2="279" y2="245"/>
      <line x1="199" y1="277" x2="233" y2="277"/><line x1="245" y1="277" x2="279" y2="277"/>
    </g>
    <circle cx="239" cy="245" r="3" fill="none" stroke="var(--white)"/>
    <circle cx="239" cy="277" r="3" fill="none" stroke="var(--white)"/>
    <text class="sans" x="239" y="262" font-size="10.5" font-weight="700" fill="var(--white)" text-anchor="middle">877-ROOF-TMD</text>
    <text class="sans" x="239" y="293" font-size="9.5" font-weight="600" fill="var(--white)" text-anchor="middle">tmdshingleworks.net</text>
  </g>
  <g class="podium-side">
    <circle cx="706" cy="111" r="17" fill="var(--brand-blue)"/>
    <text class="brand-name" x="706" y="152" font-size="16" text-anchor="middle">TMD</text>
    <text class="brand-name" x="706" y="163" font-size="7" letter-spacing="1" text-anchor="middle">SHINGLE WORKS</text>
    <g stroke="var(--white)" stroke-width="1">
      <line x1="666" y1="245" x2="700" y2="245"/><line x1="712" y1="245" x2="746" y2="245"/>
      <line x1="666" y1="277" x2="700" y2="277"/><line x1="712" y1="277" x2="746" y2="277"/>
    </g>
    <circle cx="706" cy="245" r="3" fill="none" stroke="var(--white)"/>
    <circle cx="706" cy="277" r="3" fill="none" stroke="var(--white)"/>
    <text class="sans" x="706" y="262" font-size="10.5" font-weight="700" fill="var(--white)" text-anchor="middle">877-ROOF-TMD</text>
    <text class="sans" x="706" y="293" font-size="9.5" font-weight="600" fill="var(--white)" text-anchor="middle">tmdshingleworks.net</text>
  </g>
</svg>

</body>
</html>
```